I need a complete stationary pack for a real estate office that sells and manages residential proper

We need a stationary design pack for my real estate office called ‘brightkeyhomes’ that is in Queensland Australia. My offices are both in suburban and coastal locations in the south west corner of Queensland at the Coral Bay Shore and Brisbane.
We predominately manage real estate on behalf of owners and sell property in the residential sector.
I have attached a copy of our existing design of my business card and do like the current concept/layout. In saying this you may be able to use this existing theme across to the other items required or see opportunity on how to improve what I have already.
I would like to see concepts for the following products:
- Letterhead
- Fax header
- Business cards
- Email signature
- With complements slips and
- Envelopes
I have attached our current logo that was designed by Artfolder and the font is Prelo.

I am looking for a contemporary design that is professional and reflects trust and professionalism. I am currently using the logo with a black background on some material as per the following link

http://www.plotlisting.com.au/property/for-sale/house/qld/merridale/?adid=4827305118&sp=7

I have posted another job 517362 for signage and the company car signage done too if you are interested.

Please do not hesitate to contact me should you have any questions. Thank you.

Target Market(s)

Western speaking people aged from 25 to 60 from modest backgrounds to well off individuals

Industry/Entity Type

Real Estate

Requirements
Must have
• Professional in appearance, show a mature and trustworthy image
Should not have
• As there is good colour with the logo, i am do not want over the top designs or colours

```html
<!DOCTYPE html>
<html lang="en">
<head>
<meta charset="utf-8">
<title>brightkeyhomes business card</title>
<link rel="stylesheet" href="https://fonts.googleapis.com/css2?family=Open+Sans:wght@400;600;700&display=swap">
<style>
  :root {
    --canvas: #ebe8e3;
    --card-white: #ffffff;
    --card-black: #141414;
    --ink: #4a4a4a;
    --ink-soft: #6b6b6b;
    --red: #e02a2a;
    --purple: #7b2f93;
    --blue: #1f7fc8;
    --green: #3aa84a;
    --orange: #f5a623;
    --rust: #e4602f;
    --link-green: #4caf50;
  }
  * { box-sizing: border-box; margin: 0; padding: 0; }
  html, body { width: 1200px; height: 1024px; overflow: hidden; }
  body {
    background: var(--canvas);
    font-family: "Open Sans", Arial, sans-serif;
    position: relative;
  }
  .card {
    position: absolute;
    width: 600px;
    height: 340px;
    border-radius: 22px;
    overflow: hidden;
    box-shadow: 0 10px 28px rgba(0,0,0,0.18);
  }
  /* Front */
  .card-front { left: 90px; top: 100px; background: var(--card-white); }
  .side-band {
    position: absolute; left: 0; top: 0; bottom: 0; width: 40px;
    display: flex; flex-direction: column;
  }
  .side-band .seg { height: 34px; }
  .seg-red { background: var(--red); }
  .seg-purple { background: var(--purple); }
  .seg-blue { background: var(--blue); }
  .seg-green { background: var(--green); }
  .seg-orange { background: var(--orange); }
  .seg-icons {
    flex: 1; background: var(--rust);
    display: flex; flex-direction: column; justify-content: flex-start;
    align-items: center; padding-top: 54px; gap: 3px;
  }
  .seg-icons svg { width: 12px; height: 12px; display: block; }
  .icon-slot { height: 16px; display: flex; align-items: center; }

  .profile-photo {
    position: absolute; left: 62px; top: 100px; width: 150px; height: 104px;
    background: linear-gradient(135deg, #7fa9c9 0%, #5d7890 55%, #2d3440 100%);
  }
  .person { position: absolute; left: 224px; top: 158px; }
  .person-name { color: var(--red); font-weight: 700; font-size: 19px; line-height: 1.15; }
  .person-role { color: var(--blue); font-size: 14px; margin-top: 2px; }

  .contact-list {
    position: absolute; left: 62px; top: 224px; list-style: none;
    color: var(--ink-soft); font-size: 12.5px; line-height: 19px;
  }
  .contact-list .hl { color: var(--link-green); }

  .brand {
    position: absolute; display: flex; align-items: center; gap: 10px;
  }
  .brand-dot { border-radius: 50%; flex: none; }
  .brand-name { font-weight: 600; letter-spacing: -0.3px; white-space: nowrap; }
  .card-front .brand { right: 36px; top: 30px; }
  .card-front .brand-dot { width: 30px; height: 30px; background: var(--blue); }
  .card-front .brand-name { font-size: 25px; color: var(--ink); }

  /* Back */
  .card-back {
    left: 510px; top: 570px;
    background: radial-gradient(ellipse at 55% 40%, #2a2a2a 0%, var(--card-black) 70%);
  }
  .card-back .brand { left: 50%; top: 120px; transform: translateX(-50%); }
  .card-back .brand-dot { width: 46px; height: 46px; background: var(--orange); }
  .card-back .brand-name { font-size: 40px; color: #ffffff; }
  .back-url {
    position: absolute; left: 0; right: 0; top: 210px; text-align: center;
    color: var(--link-green); font-size: 14px;
  }
</style>
</head>
<body>

<section class="card card-front">
  <div class="side-band">
    <div class="seg seg-red"></div>
    <div class="seg seg-purple"></div>
    <div class="seg seg-blue"></div>
    <div class="seg seg-green"></div>
    <div class="seg seg-orange"></div>
    <div class="seg-icons">
      <div class="icon-slot"><svg viewBox="0 0 16 16"><rect x="4" y="1" width="8" height="14" rx="1.5" fill="#fff"/><rect x="5.5" y="3" width="5" height="8" fill="#e4602f"/></svg></div>
      <div class="icon-slot"><svg viewBox="0 0 16 16"><path d="M3 2c1-1 2-1 3 1l1 2c0 1-1 1.5-1 2 1 2 2 3 4 4 .5 0 1-1 2-1l2 1c2 1 2 2 1 3-2 2-5 1-8-2S1 4 3 2z" fill="#fff"/></svg></div>
      <div class="icon-slot"><svg viewBox="0 0 16 16"><rect x="1.5" y="3.5" width="13" height="9" fill="none" stroke="#fff" stroke-width="1.6"/><path d="M1.5 3.5 8 9l6.5-5.5" fill="none" stroke="#fff" stroke-width="1.6"/></svg></div>
      <div class="icon-slot"><svg viewBox="0 0 16 16"><circle cx="8" cy="8" r="6.5" fill="none" stroke="#fff" stroke-width="1.5"/><ellipse cx="8" cy="8" rx="3" ry="6.5" fill="none" stroke="#fff" stroke-width="1.2"/><path d="M1.5 8h13" stroke="#fff" stroke-width="1.2"/></svg></div>
      <div class="icon-slot"><svg viewBox="0 0 16 16"><path d="M8 1a5 5 0 0 0-5 5c0 4 5 9 5 9s5-5 5-9a5 5 0 0 0-5-5z" fill="#fff"/><circle cx="8" cy="6" r="2" fill="#e4602f"/></svg></div>
    </div>
  </div>

  <div class="brand">
    <span class="brand-dot"></span>
    <span class="brand-name">brightkeyhomes</span>
  </div>

  <div class="profile-photo" role="img" aria-label="Portrait photo of the principal"></div>
  <div class="person">
    <p class="person-name">Marcus Delane</p>
    <p class="person-role">Principal</p>
  </div>

  <ul class="contact-list">
    <li>0412550917</li>
    <li>07 5550 2184</li>
    <li>marcus@<span class="hl">brightkeyhomes</span>.com.au</li>
    <li>www.<span class="hl">brightkeyhomes</span>.com.au</li>
    <li>shop 4, 212 harbour parade, merridale qld 4571</li>
  </ul>
</section>

<section class="card card-back">
  <div class="brand">
    <span class="brand-dot"></span>
    <span class="brand-name">brightkeyhomes</span>
  </div>
  <p class="back-url">www.brightkeyhomes.com.au</p>
</section>

</body>
</html>
```